We need a business card design for a new company located in Missouri City, TX, entitled 'BrightPath Chiropractic & Holistic Center'. Our services include restoration of health and vitality, spinal exam, health assessment, dietary & fitness programs, lymphatic & therapeutic massage, detox & remineralize body wraps, far infrared sauna therapy

Industry/Entity Type

Business

Contact Information for Business Card

BrightPath Chiropractic & Holistic Center, Marlene Okafor LMT, 4215 Elm Ridge Rd., Suite 310, Missouri City, TX 77482, 281-555-0193

```html
<!DOCTYPE html>
<html lang="en">
<head>
<meta charset="utf-8">
<title>BrightPath Chiropractic &amp; Holistic Center – Business Card</title>
<link href="https://fonts.googleapis.com/css2?family=Marcellus&family=Arimo:wght@400&display=swap" rel="stylesheet">
<style>
  :root {
    --page: #ecebe8;
    --teal: #1e9c86;
    --teal-deep: #15806f;
    --navy: #1f5f8b;
    --navy-deep: #194f75;
    --ink: #111111;
    --paper: #ffffff;
    --paper-shade: #efefef;
    --logo-grey: #6e6e6e;
    --text-light: #f4f8fa;
  }
  * { box-sizing: border-box; margin: 0; padding: 0; }
  html, body { width: 1200px; height: 902px; overflow: hidden; }
  body {
    background: var(--page);
    display: flex;
    align-items: center;
    justify-content: center;
    gap: 40px;
  }
  .card {
    width: 540px;
    height: 309px;
    position: relative;
    overflow: hidden;
    box-shadow: 0 6px 18px rgba(0,0,0,0.18);
  }

  /* Back: services */
  .card-back {
    background: linear-gradient(160deg, var(--teal) 0%, var(--teal-deep) 100%);
    color: var(--text-light);
    font-family: "Arimo", Arial, sans-serif;
    padding: 34px 40px;
  }
  .services-title { font-size: 27px; margin-bottom: 8px; }
  .services-list { list-style: none; font-size: 17px; line-height: 30px; }
  .services-list li { display: flex; align-items: center; }
  .services-list .lead { padding-left: 38px; }
  .bullet {
    width: 9px; height: 9px; border-radius: 50%;
    background: var(--text-light);
    margin-right: 29px; flex: none;
  }

  /* Front: identity */
  .card-front { background: var(--paper); }
  .front-top {
    position: absolute; inset: 0 0 auto 0; height: 172px;
    background: linear-gradient(180deg, var(--paper) 0%, var(--paper-shade) 100%);
    display: flex; align-items: center; justify-content: center;
  }
  .brand { display: flex; align-items: center; gap: 14px; color: var(--logo-grey); font-family: "Marcellus", serif; }
  .brand-dot { width: 34px; height: 34px; border-radius: 50%; background: var(--teal); flex: none; }
  .brand-text { text-align: center; line-height: 1.1; }
  .brand-name { font-size: 40px; }
  .brand-tag { font-size: 19px; }
  .front-band { position: absolute; left: 0; right: 0; top: 172px; height: 20px; background: var(--ink); }
  .front-bottom {
    position: absolute; left: 0; right: 0; top: 192px; bottom: 0;
    background: linear-gradient(180deg, var(--navy) 0%, var(--navy-deep) 100%);
    color: var(--text-light);
    padding: 12px 22px 0 26px;
  }
  .person { position: absolute; left: 26px; top: 16px; font-family: "Marcellus", serif; }
  .person-name { font-size: 30px; }
  .person-role { font-size: 20px; margin-top: 2px; }
  .contacts {
    position: absolute; left: 262px; top: 12px;
    border-left: 1px solid var(--text-light);
    padding-left: 10px;
    font-family: "Arimo", Arial, sans-serif; font-size: 14px; line-height: 22px;
  }
  .contacts li { list-style: none; display: flex; align-items: center; gap: 8px; white-space: nowrap; }
  .contacts svg { width: 14px; height: 14px; flex: none; }
  .address {
    position: absolute; left: 26px; right: 10px; bottom: 14px;
    font-family: "Arimo", Arial, sans-serif; font-size: 13px; white-space: nowrap;
  }
</style>
</head>
<body>

  <section class="card card-back" aria-label="Business card back: services">
    <h2 class="services-title">Services :</h2>
    <ul class="services-list">
      <li class="lead">Restoration of health and vitality</li>
      <li><span class="bullet"></span>Spinal exam</li>
      <li><span class="bullet"></span>Health assessment</li>
      <li><span class="bullet"></span>Dietary &amp; fitness programs</li>
      <li><span class="bullet"></span>Lymphatic &amp; therapeutic massage</li>
      <li><span class="bullet"></span>Detox &amp; remineralize body wraps</li>
      <li><span class="bullet"></span>Far infrared sauna therapy</li>
    </ul>
  </section>

  <section class="card card-front" aria-label="Business card front">
    <div class="front-top">
      <div class="brand">
        <span class="brand-dot"></span>
        <div class="brand-text">
          <div class="brand-name">BrightPath</div>
          <div class="brand-tag">Chiropractic &amp; Holistic Center</div>
        </div>
      </div>
    </div>
    <div class="front-band"></div>
    <div class="front-bottom">
      <div class="person">
        <div class="person-name">Anya Castell</div>
        <div class="person-role">Director</div>
      </div>
      <ul class="contacts">
        <li>
          <svg viewBox="0 0 14 14" aria-hidden="true"><rect width="14" height="14" rx="2" fill="#f4f8fa"/><path d="M3 4.5c0-1 1-1.5 4-1.5s4 .5 4 1.5v1H9V4.6H5v.9H3z M4 7h6l1 4H3z" fill="#1f5f8b"/></svg>
          281-555-0193
        </li>
        <li>
          <svg viewBox="0 0 14 14" aria-hidden="true"><rect width="14" height="14" rx="2" fill="#f4f8fa"/><circle cx="7" cy="7" r="4.3" fill="none" stroke="#1f5f8b" stroke-width="1.2"/><path d="M2.7 7h8.6M7 2.7c-2 2.4-2 6.2 0 8.6M7 2.7c2 2.4 2 6.2 0 8.6" fill="none" stroke="#1f5f8b" stroke-width="1"/></svg>
          www.BrightPathHolistic.com
        </li>
        <li>
          <svg viewBox="0 0 14 14" aria-hidden="true"><rect width="14" height="14" rx="2" fill="#f4f8fa"/><rect x="2.5" y="4" width="9" height="6.5" fill="none" stroke="#1f5f8b" stroke-width="1.1"/><path d="M2.5 4l4.5 3.6L11.5 4" fill="none" stroke="#1f5f8b" stroke-width="1.1"/></svg>
          acastell@brightpathholistic.com
        </li>
      </ul>
      <p class="address">Marlene Okafor LMT, 4215 Elm Ridge Rd., Suite 310, Missouri City, TX 77482</p>
    </div>
  </section>

</body>
</html>
```